Business Card Design

Attached is my current Business card I do not like it but I must save the logo portion of it. Don't like the color or the lettering am looking for more architectural look in grays or taupe with the green more of a charturese color and the blue a charcoal color on a textured paper that looks more like something high-end that would appeal to an architect or a designer. We make concrete decorative items such as concrete fireplaces, sinks, tops and more.

Target Market(s)

Architects designers of Commercial and Residential - artistic features

Industry/Entity Type

Architect

Contact Information for Business Card

Marisol T. Quenby President and Marketing Director
602-418-5093
email marisol@vantorelstone.example
Showroom "Quillmont Design Center" 4183 W Palomar Scottsdale AZ
Fax: 602-731-6624

Font styles to use
Sans Serif

Requirements
Must have
• Architectural
Natural and earthy colors with a touch of color in the existing attached

```html
<!DOCTYPE html>
<html lang="en">
<head>
<meta charset="utf-8">
<title>Vantorel Stone — Business Card</title>
<link rel="stylesheet" href="https://fonts.googleapis.com/css2?family=Exo+2:wght@300;400;500&display=swap">
<style>
  :root {
    --page: #e9e9e7;
    --card: #ebebeb;
    --card-shade: #e2e2e2;
    --navy: #34495e;
    --lime: #8db52b;
    --slate: #737373;
    --ink: #5d5d5d;
    --white: #ffffff;
  }
  * { box-sizing: border-box; margin: 0; padding: 0; }
  html, body {
    width: 1200px; height: 1000px; overflow: hidden;
    background: var(--page);
    font-family: "Exo 2", "Helvetica Neue", Arial, sans-serif;
    color: var(--ink);
  }
  .canvas { position: relative; width: 1200px; height: 1000px; }
  .card {
    position: absolute; left: 270px;
    width: 660px; height: 377px;
    background: linear-gradient(160deg, var(--card) 0%, var(--card-shade) 100%);
    box-shadow: 0 2px 6px rgba(0,0,0,.12);
    overflow: hidden;
  }
  .card--front { top: 80px; }
  .card--back { top: 523px; }

  .wordmark { display: flex; align-items: center; gap: 10px; }
  .wordmark__square { width: 16px; height: 16px; background: var(--lime); }
  .wordmark__name {
    font-weight: 400; font-size: 30px; letter-spacing: 1px;
    text-transform: uppercase; color: var(--ink);
  }
  .card--front .wordmark {
    position: absolute; top: 50%; left: 50%;
    transform: translate(-50%, -50%);
  }
  .card--back .wordmark { position: absolute; left: 40px; top: 110px; }
  .card--back .wordmark__name { font-size: 24px; }

  .band { position: absolute; left: 0; }
  .band--name {
    top: 200px; width: 390px; height: 46px;
    background: var(--navy);
    display: flex; align-items: center; justify-content: flex-end;
    padding-right: 18px;
  }
  .person-name { color: var(--white); font-weight: 400; font-size: 26px; letter-spacing: .5px; }
  .band--title {
    top: 246px; width: 390px; height: 26px;
    background: var(--lime);
    display: flex; align-items: center; justify-content: flex-end;
    padding-right: 18px;
  }
  .person-title { color: var(--white); font-weight: 300; font-size: 14px; }

  .band--contact {
    left: 390px; top: 200px; width: 270px; height: 72px;
    background: var(--slate);
    padding: 9px 14px;
    display: flex; flex-direction: column; justify-content: center; gap: 3px;
  }
  .contact-line {
    display: flex; align-items: center; gap: 7px;
    color: var(--white); font-size: 12px; font-weight: 300;
  }
  .contact-line svg { width: 11px; height: 11px; flex: none; fill: var(--white); }

  .showroom {
    position: absolute; left: 420px; top: 296px;
    font-size: 11px; line-height: 1.35; font-weight: 300; color: var(--ink);
  }
  .showroom__label { font-weight: 500; color: var(--navy); }
  .showroom__label em { font-style: normal; color: var(--lime); }
</style>
</head>
<body>
<main class="canvas">
  <section class="card card--front" aria-label="Card front">
    <div class="wordmark">
      <span class="wordmark__square"></span>
      <span class="wordmark__name">Vantorel Stone</span>
    </div>
  </section>

  <section class="card card--back" aria-label="Card back">
    <div class="wordmark">
      <span class="wordmark__square"></span>
      <span class="wordmark__name">Vantorel Stone</span>
    </div>

    <div class="band band--name"><h1 class="person-name">Marisol T. Quenby</h1></div>
    <div class="band band--title"><p class="person-title">President &amp; Marketing Director</p></div>

    <div class="band band--contact">
      <p class="contact-line">
        <svg viewBox="0 0 24 24" aria-hidden="true"><path d="M6.6 10.8a15 15 0 0 0 6.6 6.6l2.2-2.2c.3-.3.7-.4 1-.2 1.1.4 2.3.6 3.6.6.6 0 1 .4 1 1V20c0 .6-.4 1-1 1A17 17 0 0 1 3 4c0-.6.4-1 1-1h3.5c.6 0 1 .4 1 1 0 1.3.2 2.5.6 3.6.1.3 0 .7-.2 1z"/></svg>
        602-418-5093
      </p>
      <p class="contact-line">
        <svg viewBox="0 0 24 24" aria-hidden="true"><path d="M6 3h10v5H6zM3 9h18v9h-3v3H6v-3H3zm5 6v4h8v-4z"/></svg>
        602-731-6624
      </p>
      <p class="contact-line">
        <svg viewBox="0 0 24 24" aria-hidden="true"><path d="M2 5h20v14H2zm2 2v.5l8 5 8-5V7z"/></svg>
        marisol@vantorelstone.example
      </p>
    </div>

    <address class="showroom">
      <span class="showroom__label">Vantorel Stone <em>Showroom</em></span><br>
      "Quillmont Design Center" 4183 W Palomar<br>
      Scottsdale AZ
    </address>
  </section>
</main>
</body>
</html>
```